Film Production Company Needs HTML Website Design

My production company, QuillanStudioWorks.com , needs to have an HTML design of our website. I would like a minotaur as the company symbol, as well as a hellfire in the background. Something dark and edgy, like we currently have, but different. The password to open the attached zip file is: KTRW3mze81Pvd62JGsQe
Please check out our website and include all of the tabs that are currently in the design, especially the Investor section.

Film Production

```html
<!DOCTYPE html>
<html lang="en">
<head>
<meta charset="utf-8">
<title>Quillan Studio Productions</title>
<link href="https://fonts.googleapis.com/css2?family=Cinzel:wght@400;700&family=Marcellus&family=Tinos&family=Montserrat:wght@400;500&family=Oswald:wght@400&display=swap" rel="stylesheet">
<style>
:root{
  --page:#ffffff;
  --black:#000000;
  --deep-red:#2a0202;
  --glow-red:#8c0c06;
  --gold:#f0c232;
  --orange:#e48a1a;
  --nav-red:#d8202a;
  --nav-gold:#e2b035;
  --tagline:#c5101e;
  --body:#f3d6b4;
  --link:#f0c48a;
}
*{margin:0;padding:0;box-sizing:border-box}
html,body{width:1200px;height:1000px;overflow:hidden;background:var(--page)}
.canvas{position:relative;width:1200px;height:1000px}
.site{position:absolute;left:50px;top:48px;width:1108px;height:920px;background:var(--black);overflow:hidden}
.site-glow{position:absolute;left:0;top:115px;width:1108px;height:805px;
  background:radial-gradient(ellipse 70% 55% at 50% 30%,#3a0403 0%,var(--deep-red) 55%,#0a0000 100%)}
.abs{position:absolute;white-space:nowrap}
.logo-box{left:286px;top:22px;width:590px;height:113px;background:var(--black)}
.logo-name{left:286px;top:44px;width:590px;text-align:center;font:700 62px/1 "Cinzel",serif;color:var(--orange);letter-spacing:1px}
.tagline{left:418px;top:148px;width:360px;text-align:center;font:400 17px/1 "Cinzel",serif;color:var(--tagline);letter-spacing:20px}
.nav{left:12px;top:202px;width:1080px;height:47px;background:var(--black);border-radius:8px;
  box-shadow:0 0 0 3px #3c0302,0 0 12px 4px var(--glow-red)}
.nav-item{position:absolute;top:13px;font:400 18px/1 "Marcellus",serif;color:var(--nav-red);letter-spacing:1px;white-space:nowrap}
.nav-item.is-active{color:var(--nav-gold)}
.nav-sep{position:absolute;top:10px;width:1px;height:26px;background:#333}
.panel{border-radius:8px;box-shadow:0 0 0 3px #3a0302,0 0 14px 4px var(--glow-red);
  background:radial-gradient(ellipse 80% 60% at 30% 20%,#7a0e06 0%,#3c0302 45%,#140000 100%)}
.panel.dark{background:radial-gradient(ellipse 60% 40% at 20% 15%,#6a1206 0%,#1c0201 50%,#0a0000 100%)}
.heading{font:700 40px/1 "Cinzel",serif;color:var(--gold);
  background:linear-gradient(#ffe04a,#e58a12);-webkit-background-clip:text;background-clip:text;-webkit-text-fill-color:transparent}
.subheading{font:400 16px/1 "Cinzel",serif;color:var(--gold);letter-spacing:7px}
.copy{font:400 12px/18px "Tinos",serif;color:var(--body);white-space:normal}
.pill{font:400 10px/14px "Montserrat",sans-serif;color:var(--link);background:#3a0e06;border-radius:8px;padding:0 9px}
.list{list-style:none;font:400 10px/1 "Montserrat",sans-serif;color:var(--link);width:120px}
.list li{position:absolute;left:0;white-space:nowrap}
.list li::before{content:"›";position:absolute;left:-15px;top:-1px;color:var(--body);font-size:12px}
.more{font:500 10px/1 "Montserrat",sans-serif;color:var(--body)}
.hero{left:370px;top:282px;width:370px;height:560px;
  background:radial-gradient(ellipse 45% 50% at 50% 55%,#f39a2a 0%,#c4420e 35%,rgba(74,10,2,.6) 70%,rgba(0,0,0,0) 100%)}
.film{left:834px;top:346px;width:204px;height:144px;background:#0c0000}
.frame{position:absolute;width:74px;height:58px;background:#120000;border:1px solid #200303;
  font:400 21px/58px "Oswald",sans-serif;color:#e99a2a;text-align:center}
.social{position:absolute;top:865px;width:36px;height:29px;background:#1c140c}
.footer{left:0;top:875px;width:1086px;text-align:center;font:400 10px/1 "Montserrat",sans-serif;color:var(--link)}
</style>
</head>
<body>
<div class="canvas">
  <div class="site">
    <div class="site-glow"></div>

    <div class="abs logo-box"></div>
    <div class="abs logo-name">QUILLAN STUDIO</div>
    <div class="abs tagline">PRODUCTIONS</div>

    <nav class="abs nav">
      <span class="nav-item is-active" style="left:110px">Home</span>
      <span class="nav-sep" style="left:203px"></span>
      <span class="nav-item" style="left:240px">About Us</span>
      <span class="nav-sep" style="left:366px"></span>
      <span class="nav-item" style="left:403px">News</span>
      <span class="nav-sep" style="left:486px"></span>
      <span class="nav-item" style="left:522px">Productions</span>
      <span class="nav-sep" style="left:671px"></span>
      <span class="nav-item" style="left:699px">Investors</span>
      <span class="nav-sep" style="left:833px"></span>
      <span class="nav-item" style="left:860px">Contact Us</span>
    </nav>

    <section class="abs panel" style="left:17px;top:274px;width:300px;height:264px"></section>
    <h1 class="abs heading" style="left:55px;top:284px">WELCOME</h1>
    <div class="abs subheading" style="left:48px;top:336px">TO OUR WEBSITE</div>
    <p class="abs copy" style="left:47px;top:381px;width:258px">Sed laoreet aliquam leo ut tellus dolor dapibus eget elementum vel cursus eleifend elit Aenean auctor wisi et urna aliquam erat volutpat. Duis ac turpis. Integer rutrum ante eu lacus.</p>
    <span class="abs pill" style="left:156px;top:495px">Click here to read more ›</span>

    <section class="abs panel" style="left:17px;top:562px;width:300px;height:252px"></section>
    <h2 class="abs heading" style="left:63px;top:578px;font-size:34px">QUILLAN</h2>
    <div class="abs subheading" style="left:50px;top:622px;letter-spacing:11px">PROJECTS</div>
    <ul class="abs list" style="left:45px;top:675px">
      <li style="top:0">Project 1</li>
      <li style="top:17px">Project 2</li>
      <li style="top:35px">Project 3</li>
      <li style="top:53px">Project 4</li>
      <li style="top:72px">Project 5</li>
    </ul>
    <span class="abs more" style="left:230px;top:788px">Read more ›</span>

    <div class="abs hero" role="img" aria-label="Minotaur warrior holding an axe, standing in hellfire"></div>

    <section class="abs panel" style="left:797px;top:274px;width:287px;height:262px"></section>
    <h2 class="abs heading" style="left:816px;top:287px;font-size:31px">LATEST WORKS</h2>
    <div class="abs film">
      <div class="frame" style="left:16px;top:10px">PHOTO</div>
      <div class="frame" style="left:114px;top:10px">PHOTO</div>
      <div class="frame" style="left:16px;top:74px">PHOTO</div>
      <div class="frame" style="left:114px;top:74px">PHOTO</div>
    </div>
    <span class="abs pill" style="left:974px;top:509px">More gallery ›</span>

    <section class="abs panel dark" style="left:797px;top:562px;width:291px;height:252px"></section>
    <h2 class="abs heading" style="left:888px;top:584px;font-size:32px">NEWS</h2>
    <ul class="abs list" style="left:835px;top:657px">
      <li style="top:0">News 1</li>
      <li style="top:31px">News 2</li>
      <li style="top:62px">News 3</li>
      <li style="top:88px">News 4</li>
      <li style="top:114px">News 5</li>
    </ul>
    <span class="abs more" style="left:1004px;top:794px">Read more ›</span>

    <div class="social" style="left:22px" aria-label="Social link"></div>
    <div class="social" style="left:63px" aria-label="Social link"></div>
    <div class="social" style="left:105px" aria-label="Social link"></div>
    <div class="social" style="left:147px" aria-label="Social link"></div>

    <div class="abs footer">Quillan Studio © 2014 . Privacy Policy</div>
  </div>
</div>
</body>
</html>
```